Business Card Design for a Software Startup

We'd like to have a business card design. We already have a logo. Basically what we need is a clean design with name, address, cellphone and phone numbers, e-mail and web site address (front) and a space on the back with our logo with the company name on the right side and some texts on the bottom.
We are a development and consulting company in Brazil with highly qualified team of professionals in Java, iOS and Android development and consulting.

Target Market(s)

CIO, IT managers of mid to big size companies

Industry/Entity Type

Business

```html
<!DOCTYPE html>
<html lang="en">
<head>
<meta charset="utf-8">
<title>Vantel Business Card</title>
<link rel="stylesheet" href="https://fonts.googleapis.com/css2?family=Arimo:wght@400;700&family=Michroma&display=swap">
<style>
  :root {
    --backdrop: #e6e7ec;
    --card-white: #ffffff;
    --navy: #0d3766;
    --navy-deep: #0a2c55;
    --ocean: #0b4b80;
    --cyan: #0aa6e6;
    --text-light: #ffffff;
    --divider: #5b7aa6;
  }
  * { margin: 0; padding: 0; box-sizing: border-box; }
  html, body {
    width: 1200px;
    height: 987px;
    overflow: hidden;
    background: var(--backdrop);
    font-family: "Arimo", Arial, sans-serif;
  }
  .stage {
    position: relative;
    width: 1200px;
    height: 987px;
  }
  .card {
    position: absolute;
    width: 700px;
    height: 400px;
    border-radius: 26px;
    overflow: hidden;
    box-shadow: 0 10px 30px rgba(20, 30, 60, 0.18);
  }

  /* Front card */
  .card-front {
    left: 250px;
    top: 70px;
    background: var(--card-white);
  }
  .front-brand {
    position: absolute;
    left: 60px;
    top: 60px;
    display: flex;
    align-items: center;
    gap: 22px;
  }
  .brand-square {
    width: 64px;
    height: 64px;
    background: var(--navy);
  }
  .brand-name {
    font-family: "Michroma", "Arimo", sans-serif;
    font-size: 72px;
    font-weight: 400;
    letter-spacing: 2px;
    color: var(--navy);
    line-height: 1;
  }
  .info-band {
    position: absolute;
    left: 0;
    top: 200px;
    width: 100%;
    height: 150px;
    background: var(--navy);
    display: flex;
    align-items: center;
    color: var(--text-light);
    font-size: 19px;
    line-height: 1.35;
  }
  .address-block {
    width: 330px;
    padding-left: 40px;
    text-align: right;
    padding-right: 26px;
  }
  .band-divider {
    width: 1px;
    height: 110px;
    background: var(--divider);
  }
  .contact-list {
    list-style: none;
    padding-left: 26px;
  }
  .footer-strip {
    position: absolute;
    left: 0;
    top: 350px;
    width: 100%;
    height: 50px;
    background: var(--cyan);
    color: var(--text-light);
    font-size: 19px;
    display: flex;
    align-items: center;
    padding-left: 40px;
  }

  /* Back card */
  .card-back {
    left: 250px;
    top: 517px;
    background: linear-gradient(160deg, var(--ocean) 0%, var(--navy-deep) 100%);
  }
  .back-brand {
    position: absolute;
    left: 0;
    top: 130px;
    width: 100%;
    text-align: center;
    font-family: "Michroma", "Arimo", sans-serif;
    font-size: 92px;
    letter-spacing: 3px;
    color: var(--text-light);
    line-height: 1;
  }
  .back-web {
    position: absolute;
    left: 0;
    top: 270px;
    width: 100%;
    text-align: center;
    font-size: 22px;
    font-weight: 700;
    letter-spacing: 7px;
    color: var(--text-light);
  }
</style>
</head>
<body>
<main class="stage">
  <section class="card card-front" aria-label="Card front">
    <div class="front-brand">
      <span class="brand-square"></span>
      <span class="brand-name">VANTEL</span>
    </div>
    <div class="info-band">
      <p class="address-block">Door No. Street Name<br>City Name, State, Zip Code</p>
      <span class="band-divider"></span>
      <ul class="contact-list">
        <li>p: 123-456-7890</li>
        <li>c: 123-456-7890</li>
        <li>e: yourname@vantel.com</li>
        <li>w: www.vantel.com</li>
      </ul>
    </div>
    <p class="footer-strip">Door No. Street Name City Name, State, Zip Code.</p>
  </section>

  <section class="card card-back" aria-label="Card back">
    <p class="back-brand">VANTEL</p>
    <p class="back-web">www.vantel.com</p>
  </section>
</main>
</body>
</html>
```